Need Help having my business card stand out

I am the owner of Birchway Canine Training and would like for my business cards to stand out. I have been trying to keep designing them myself but I can't get what I have in my head on the card. I will try my best to post templates that I like for inspirations. I want something unique but elegant. I don't want in to look cartoony or cheesy. It needs to pop in a pet shop but also in a coffee shop or gym.

Target Market(s)

Dog owners, Married ,No young kids Jr High school kids and up (maybe kids on the way) Executives, Stay at home moms/wives, Small business owners

Industry/Entity Type

Dog Training

Contact Information for Business Card

Lowell Spratt, 281-904-3376, info@birchwaycanine.example, www.birchwaycanine.example

Colors

Designer to choose colors to be used in the design.

Requirements
Must have
• my logo
Should not have
• Cursive lettering

```html
<!DOCTYPE html>
<html lang="en">
<head>
<meta charset="utf-8">
<title>Birchway Canine Training – Business Card</title>
<link href="https://fonts.googleapis.com/css2?family=Montserrat:wght@400;600;700&display=swap" rel="stylesheet">
<style>
  :root {
    --bg: #dcd0c8;
    --brown-dark: #7a3a2a;
    --brown: #9c5440;
    --brown-warm: #b8674f;
    --brown-light: #c98a74;
    --blush: #ecd6cd;
    --white: #ffffff;
    --ink-soft: #b0705c;
  }
  * { box-sizing: border-box; margin: 0; padding: 0; }
  html, body { width: 1200px; height: 800px; overflow: hidden; }
  body {
    background: var(--bg);
    font-family: "Montserrat", sans-serif;
    position: relative;
  }
  .card {
    position: absolute;
    top: 245px;
    width: 540px;
    height: 309px;
    overflow: hidden;
    box-shadow: 0 10px 24px rgba(90, 50, 35, 0.22);
  }
  /* Front */
  .card--front {
    left: 40px;
    background: linear-gradient(135deg, var(--brown) 0%, var(--brown-warm) 55%, var(--brown) 100%);
  }
  .front__photo {
    position: absolute;
    left: 70px;
    top: 20px;
    width: 260px;
    height: 260px;
    border-radius: 50%;
    background: radial-gradient(circle at 50% 45%, rgba(230,180,160,0.55) 0%, rgba(200,130,105,0.35) 45%, rgba(180,100,80,0) 72%);
  }
  .brand {
    position: absolute;
    right: 30px;
    top: 32px;
    display: flex;
    align-items: center;
    gap: 10px;
  }
  .brand__mark {
    width: 18px;
    height: 18px;
    border-radius: 50%;
    background: var(--brown-dark);
  }
  .brand__name {
    color: var(--brown-dark);
    font-weight: 700;
    font-size: 17px;
    line-height: 1.15;
    width: 150px;
  }
  .front__rule {
    position: absolute;
    left: 0; right: 0;
    bottom: 46px;
    height: 6px;
    background: var(--brown-dark);
    opacity: 0.55;
  }
  .front__band {
    position: absolute;
    right: 0;
    bottom: 52px;
    width: 300px;
    height: 44px;
    background: var(--brown-dark);
    clip-path: polygon(22px 0, 100% 0, 100% 100%, 0 100%);
    display: flex;
    align-items: center;
    justify-content: flex-end;
    padding-right: 22px;
  }
  .tagline {
    color: var(--white);
    font-size: 19px;
    font-weight: 400;
    letter-spacing: 0.5px;
  }
  /* Back */
  .card--back {
    left: 620px;
    background: var(--white);
  }
  .back__texture {
    position: absolute;
    right: 0; top: 0;
    width: 100%;
    height: 150px;
    background: linear-gradient(160deg, rgba(255,255,255,0) 20%, var(--blush) 70%, rgba(201,138,116,0.45) 100%);
    clip-path: polygon(30% 0, 100% 0, 100% 100%, 0 100%);
  }
  .back__band {
    position: absolute;
    right: 0;
    top: 62px;
    width: 330px;
    height: 46px;
    background: linear-gradient(90deg, rgba(184,103,79,0.75), var(--brown-warm));
    clip-path: polygon(0 0, 100% 0, 100% 100%, 12px 100%);
    padding: 5px 0 0 40px;
  }
  .person__name {
    color: var(--white);
    font-weight: 700;
    font-size: 18px;
    line-height: 1.1;
  }
  .person__role {
    color: var(--brown-dark);
    font-size: 10px;
    letter-spacing: 1.5px;
    opacity: 0.7;
  }
  .paws {
    position: absolute;
    background: radial-gradient(circle, rgba(201,138,116,0.8) 0%, rgba(201,138,116,0.55) 60%, rgba(201,138,116,0) 72%);
  }
  .paws--left { left: 28px; top: 130px; width: 60px; height: 60px; }
  .paws--right { right: 40px; top: 120px; width: 46px; height: 30px; }
  .contact {
    position: absolute;
    left: 28px;
    bottom: 26px;
    list-style: none;
    display: flex;
    flex-direction: column;
    gap: 6px;
  }
  .contact__item {
    display: flex;
    align-items: center;
    gap: 10px;
    color: var(--ink-soft);
    font-size: 12px;
  }
  .contact__icon { width: 14px; height: 14px; flex: none; }
</style>
</head>
<body>
  <section class="card card--front" aria-label="Business card front">
    <div class="front__photo" role="img" aria-label="Soft-toned photograph of a smiling corgi"></div>
    <div class="brand">
      <span class="brand__mark"></span>
      <span class="brand__name">Birchway Canine Training</span>
    </div>
    <div class="front__band"><p class="tagline">your dog trainer for life</p></div>
    <div class="front__rule"></div>
  </section>

  <section class="card card--back" aria-label="Business card back">
    <div class="back__texture" role="img" aria-label="Faint decorative lattice pattern"></div>
    <div class="back__band">
      <p class="person__name">Lowell Spratt</p>
      <p class="person__role">FOUNDER</p>
    </div>
    <div class="paws paws--left" role="img" aria-label="Paw print decoration"></div>
    <div class="paws paws--right" role="img" aria-label="Paw print decoration"></div>
    <ul class="contact">
      <li class="contact__item">
        <svg class="contact__icon" viewBox="0 0 14 14"><circle cx="7" cy="7" r="7" fill="#c98a74"/><path d="M7 3.2a2.4 2.4 0 0 0-2.4 2.4C4.6 7.4 7 10.6 7 10.6s2.4-3.2 2.4-5A2.4 2.4 0 0 0 7 3.2z" fill="#fff"/></svg>
        000 Alder Lane, Suite 300, Fairview, US 0000
      </li>
      <li class="contact__item">
        <svg class="contact__icon" viewBox="0 0 14 14"><circle cx="7" cy="7" r="7" fill="#c98a74"/><path d="M4.5 3.5l1.6 0 .6 1.8-.9.7a5 5 0 0 0 2.2 2.2l.7-.9 1.8.6v1.6c-3.6.3-6.3-2.4-6-6z" fill="#fff"/></svg>
        281-904-3376
      </li>
      <li class="contact__item">
        <svg class="contact__icon" viewBox="0 0 14 14"><circle cx="7" cy="7" r="7" fill="#c98a74"/><rect x="3.5" y="4.5" width="7" height="5" fill="#fff"/><path d="M3.5 4.5L7 7.3l3.5-2.8" fill="none" stroke="#c98a74" stroke-width="0.8"/></svg>
        info@birchwaycanine.example
      </li>
      <li class="contact__item">
        <svg class="contact__icon" viewBox="0 0 14 14"><circle cx="7" cy="7" r="7" fill="#c98a74"/><circle cx="7" cy="7" r="3.6" fill="none" stroke="#fff" stroke-width="0.9"/><ellipse cx="7" cy="7" rx="1.5" ry="3.6" fill="none" stroke="#fff" stroke-width="0.9"/><path d="M3.4 7h7.2" stroke="#fff" stroke-width="0.9"/></svg>
        www.birchwaycanine.example
      </li>
    </ul>
  </section>
</body>
</html>
```